Tide & Thistle Website Creation For Online Spirits Sales via MerrowVats.com

Want a Website developed that I will use to partner with Merrow Vats to sell my signature rum online. Merrow Vats will add the final code to make the website an e-commerce site. Website should have links to Social media pages, recipies, About, news and events, products. I have he domain name already just need a designer to make the website look professional. Need website capable of being viewed on iPhone and Android devices. Please use the color scheme that is on the label. The brand motto is: Celebrate Life With Family old and new friends. The bottle sent in the images will be replaced with and actual high resolution image of the bottle when it is produce on 27 DEC 21. Can give the selected designer access to develop the website. I have the hostbramble.com domain name. Final code will be added by a designer from MerrowVats.com to make it a e-commerce store.
Updates

I added more information to refine the design I wanted. I should have had this information available to the designers when I started the project.

Target Market(s)

Target Market is 25-50 year old who drink rum

Industry/Entity Type

Spirits. Using Website to sell Rum online

Number of Pages Required

1 page

Font styles to use
Sans Serif

Colors
00AB8E
00BBA5
67D7C9
C6EFE9
E9F9F6

Requirements
Must have
• Must look elegant and of high class. Rum is being market as a premium unnamed rum.
Nice to have
• Video of people drinking, smiling and celebrating

```html
<!DOCTYPE html>
<html lang="en">
<head>
<meta charset="utf-8">
<title>Tide &amp; Thistle — Small Batch Crafted Rum</title>
<link href="https://fonts.googleapis.com/css2?family=Cinzel:wght@500;600;700&family=Great+Vibes&family=Montserrat:wght@400;500;600;700&display=swap" rel="stylesheet">
<style>
:root{
  --teal:#00AB8E;
  --teal-2:#00BBA5;
  --teal-3:#67D7C9;
  --mint:#C6EFE9;
  --mist:#E9F9F6;
  --ink:#1f1f1f;
  --text:#555;
  --white:#fff;
  --star:#F5A623;
  --gold:#F2C23A;
  --badge:#F26522;
  --serif:'Cinzel',serif;
  --script:'Great Vibes',cursive;
  --sans:'Montserrat',sans-serif;
}
*{box-sizing:border-box;margin:0;padding:0}
html,body{width:1200px;height:4255px;overflow:hidden}
body{position:relative;background:var(--white);font-family:var(--sans);color:var(--ink)}
.abs{position:absolute}
.photo{position:absolute}

/* header / hero */
.hero{position:absolute;left:0;top:0;width:1200px;height:760px;overflow:hidden;
  background:linear-gradient(160deg,#1a1d1f 0%,#3a3f40 35%,#6b6a62 60%,#2e2a24 100%)}
.hero-photo{left:0;top:0;width:1200px;height:760px;
  background:radial-gradient(ellipse at 72% 45%,rgba(226,190,120,.45),transparent 45%),
             radial-gradient(ellipse at 60% 80%,rgba(170,120,70,.55),transparent 40%),
             linear-gradient(180deg,rgba(0,0,0,.45),rgba(0,0,0,.1) 40%,rgba(0,0,0,.3))}
.brand{position:absolute;left:115px;top:18px;display:flex;align-items:center;gap:14px;color:var(--white);
  font-family:var(--serif);font-weight:600;font-size:31px;letter-spacing:1px}
.brand .dot{width:56px;height:56px;border-radius:50%;border:3px solid var(--white)}
.nav{position:absolute;top:36px;left:0;font-size:12px;font-weight:500;color:var(--white);letter-spacing:.3px}
.nav a{position:absolute;white-space:nowrap;color:inherit;text-decoration:none}
.nav a.active{font-weight:700}
.nav a.active::after{content:"";position:absolute;left:0;right:0;top:24px;height:2px;background:var(--teal)}
.hero-script{left:112px;top:236px;font-family:var(--script);font-size:64px;color:var(--white)}
.hero-title{left:112px;top:308px;font-family:var(--serif);font-weight:600;font-size:56px;line-height:56px;color:var(--white);letter-spacing:1px}
.btn-outline-light{left:127px;top:443px;width:187px;height:48px;border:2px solid var(--white);color:var(--white);
  font-size:14px;font-weight:700;display:flex;align-items:center;justify-content:center}

/* about */
.frame{border:4px solid var(--teal-3)}
.script{font-family:var(--script);color:var(--teal);font-size:46px;line-height:1}
.heading{font-family:var(--serif);font-weight:600;font-size:33px;letter-spacing:1px;color:var(--ink);line-height:1.2}
.para{font-size:15px;line-height:23px;color:var(--text)}
.btn{display:flex;align-items:center;justify-content:center;font-weight:700;font-size:15px;color:var(--white);background:var(--teal)}

/* products */
.products{left:0;top:1369px;width:1200px;height:689px;background:var(--mist)}
.card-active{left:436px;top:1579px;width:316px;height:372px;background:var(--white);box-shadow:0 4px 18px rgba(0,0,0,.06)}
.product{position:absolute;width:260px;text-align:center}
.product .bottle{width:240px;height:328px;margin:0 auto;
  background:linear-gradient(180deg,transparent 0%,#e6a05a 25%,#c2682e 60%,#7a4d2e 82%,#5a3a22 100%);border-radius:30px 30px 8px 8px}
.product h3{font-size:16px;font-weight:700;margin-top:30px;color:#333}
.product .price{font-size:19px;color:#555;margin-top:4px}
.product .price small{font-size:12px}
.stars{color:var(--star);font-size:22px;letter-spacing:2px;margin-top:6px}
.arrow{position:absolute;width:24px;height:40px}

/* recipes */
.recipes{left:0;top:2579px;width:1200px;height:640px;background:linear-gradient(160deg,var(--teal) 0%,var(--teal-2) 45%,var(--teal-3) 100%)}
.recipe{position:absolute;top:2727px;width:482px;height:310px;overflow:hidden;
  background:linear-gradient(90deg,#050505 0%,#0d0d0d 40%,#6a3a14 75%,#b8742a 100%)}
.recipe h3{position:absolute;left:50px;top:60px;color:var(--white);font-size:20px;font-weight:700}
.recipe .rule{position:absolute;left:50px;top:92px;width:40px;height:3px;background:var(--white)}
.recipe ul{position:absolute;left:50px;top:108px;list-style:none;color:var(--white);font-size:12px;font-weight:500;line-height:26.5px}
.pill{position:absolute;left:43px;top:225px;width:136px;height:33px;border-radius:17px;background:var(--teal);color:var(--white);
  font-size:11px;font-weight:700;display:flex;align-items:center;justify-content:center}

/* news */
.badge{position:absolute;background:var(--badge);color:var(--white);font-size:10px;font-weight:600;display:flex;align-items:center;justify-content:center}
.news-box{position:absolute;left:843px;width:231px;height:182px;border:1.5px solid var(--mint);border-left:none;background:var(--white)}
.news-box h4{position:absolute;left:23px;top:66px;font-size:12px;font-weight:700;color:#333}
.news-box p{position:absolute;left:23px;top:92px;width:195px;font-size:11px;line-height:20px;color:#777}

/* footer */
.footer{left:0;top:3848px;width:1200px;height:407px;background:linear-gradient(180deg,#2cc2a6,#3ccdb3);color:var(--white)}
.footer h5{position:absolute;font-family:var(--serif);font-weight:500;font-size:16px;letter-spacing:1px}
.footer a{position:absolute;font-size:12px;color:rgba(255,255,255,.9);text-decoration:none;white-space:nowrap}
.footer .vline{position:absolute;top:78px;width:1.5px;height:173px;background:rgba(255,255,255,.6)}
.social{position:absolute;top:209px;width:38px;height:38px;border-radius:50%;border:2px solid var(--white)}
.contact{position:absolute;left:944px;font-size:12px;line-height:18px}
</style>
</head>
<body>

<!-- HERO -->
<section class="hero">
  <div class="photo hero-photo" role="img" aria-label="Bartender pouring rum from a shaker into a glass over ice, with rosemary and orange peel on a wooden board"></div>
  <div class="brand"><span class="dot"></span>TIDE &amp; THISTLE</div>
  <nav class="nav">
    <a class="active" style="left:502px">ABOUT US</a>
    <a style="left:623px">PRODUCTS</a>
    <a style="left:746px">RECIPIES</a>
    <a style="left:855px">NEWS &amp; EVENT</a>
  </nav>
  <svg class="abs" style="left:1028px;top:34px" width="80" height="24" viewBox="0 0 80 24" aria-label="Search and cart">
    <circle cx="9" cy="10" r="6.5" fill="none" stroke="#fff" stroke-width="1.6"/><line x1="14" y1="15" x2="19" y2="20" stroke="#fff" stroke-width="1.6"/>
    <rect x="50" y="7" width="15" height="15" fill="none" stroke="#fff" stroke-width="1.6"/><path d="M54 7V4a3.5 3.5 0 0 1 7 0v3" fill="none" stroke="#fff" stroke-width="1.6"/>
  </svg>
  <div class="abs hero-script">Caribbean Rum</div>
  <h1 class="abs hero-title">SMALL BATCH<br>CRAFTED RUM</h1>
  <a class="abs btn-outline-light">SHOP NOW</a>
  <svg class="abs" style="left:780px;top:284px" width="84" height="84" viewBox="0 0 84 84" aria-label="Play video">
    <circle cx="42" cy="42" r="38" fill="rgba(0,0,0,.15)" stroke="#fff" stroke-width="4"/>
    <path d="M34 27 L58 42 L34 57 Z" fill="#fff"/>
  </svg>
  <svg class="abs" style="left:0;top:640px" width="1200" height="120" viewBox="0 0 1200 120">
    <path d="M0 120 Q560 -20 1200 90 L1200 120 Z" fill="#fff"/>
    <path d="M80 110 Q560 -6 1100 82" fill="none" stroke="var(--teal)" stroke-width="4"/>
  </svg>
</section>

<!-- ABOUT -->
<section>
  <div class="abs frame" style="left:86px;top:823px;width:180px;height:180px;border-right:none;border-bottom:none"></div>
  <div class="abs" style="left:552px;top:1184px;width:34px;height:68px;border-right:4px solid var(--teal-3);border-bottom:4px solid var(--teal-3)"></div>
  <div class="photo" style="left:107px;top:848px;width:331px;height:331px;background:linear-gradient(150deg,#3a2a1c,#7a5a2a 40%,#4a6a2a 70%,#2c2a22)" role="img" aria-label="Rum cocktail with crushed ice and lime"></div>
  <div class="photo" style="left:451px;top:924px;width:121px;height:112px;background:linear-gradient(160deg,#c66a1e,#7a2e10 60%,#3a1a0c)" role="img" aria-label="Rum glass in warm light"></div>
  <div class="photo" style="left:261px;top:1051px;width:311px;height:192px;background:linear-gradient(150deg,#d8dde0,#c6d2b8 50%,#8aa060)" role="img" aria-label="Two lime drinks with straws and mint"></div>
  <div class="photo" style="left:160px;top:984px;width:104px;height:281px;border-radius:30px 30px 14px 14px;background:linear-gradient(180deg,#e9e2d6 0%,#d99a4a 30%,#b2642a 70%,#8a4a20)" role="img" aria-label="Tide and Thistle rum bottle"></div>

  <div class="abs script" style="left:666px;top:860px">Who we are</div>
  <h2 class="abs heading" style="left:666px;top:906px">ABOUT TIDE &amp; THISTLE</h2>
  <div class="abs" style="left:666px;top:950px;width:50px;height:3px;background:var(--teal)"></div>
  <p class="abs para" style="left:666px;top:983px;width:448px">Lorem ipsum dolor sit amet, consectetur adipiscing elit, sed do eiusmod tempor incididunt ut labore et dolore magna aliqua. Ut enim ad minim veniam, quis nostrud exercitation ullamco laboris nisi ut aliquip ex ea commodo consequat.</p>
  <p class="abs para" style="left:666px;top:1097px;width:448px">Ut enim ad minim veniam, quis nostrud exercitation ullamco laboris nisi ut aliquip ex ea commodo consequat.</p>
  <a class="abs btn" style="left:668px;top:1190px;width:190px;height:50px">LEARN MORE</a>
</section>

<!-- PRODUCTS -->
<section>
  <div class="abs products"></div>
  <div class="abs" style="left:598px;top:1336px;width:2px;height:77px;background:var(--teal)"></div>
  <h2 class="abs heading" style="left:0;width:1200px;top:1422px;text-align:center"><span style="color:var(--teal)">OUR</span> PRODUCTS</h2>
  <div class="abs card-active"></div>
  <div class="product" style="left:131px;top:1507px">
    <div class="bottle" role="img" aria-label="Amber rum bottle on a wooden stand"></div>
    <h3>TIDE &amp; THISTLE RUM</h3><div class="price"><small>$</small>45.00</div><div class="stars">★★★★★</div>
  </div>
  <div class="product" style="left:464px;top:1507px">
    <div class="bottle" role="img" aria-label="Golden rum bottle on a wooden stand"></div>
    <h3>TIDE &amp; THISTLE RUM</h3><div class="price"><small>$</small>45.00</div>
  </div>
  <a class="abs btn" style="left:522px;top:1927px;width:161px;height:42px;font-size:13px">SHOP NOW</a>
  <div class="product" style="left:801px;top:1507px">
    <div class="bottle" role="img" aria-label="Dark rum bottle on a wooden stand"></div>
    <h3>TIDE &amp; THISTLE RUM</h3><div class="price"><small>$</small>45.00</div><div class="stars">★★★★★</div>
  </div>
  <svg class="arrow" style="left:94px;top:1707px" viewBox="0 0 24 40"><path d="M20 3 L5 20 L20 37" fill="none" stroke="#8a8a8a" stroke-width="4"/></svg>
  <svg class="arrow" style="left:1104px;top:1707px" viewBox="0 0 24 40"><path d="M4 3 L19 20 L4 37" fill="none" stroke="#8a8a8a" stroke-width="4"/></svg>
</section>

<!-- CELEBRATING -->
<section>
  <svg class="abs" style="left:0;top:2058px" width="1200" height="521" viewBox="0 0 1200 521">
    <defs>
      <linearGradient id="friendsTone" x1="0" y1="0" x2="1" y2="1">
        <stop offset="0" stop-color="#1f4e7a"/><stop offset=".5" stop-color="#3d6a90"/><stop offset=".8" stop-color="#c88a4a"/><stop offset="1" stop-color="#e2a860"/>
      </linearGradient>
    </defs>
    <ellipse cx="1210" cy="300" rx="640" ry="640" fill="var(--teal-3)"/>
    <ellipse cx="1222" cy="310" rx="636" ry="640" fill="url(#friendsTone)" role="img" aria-label="Friends laughing and toasting with drinks outdoors"/>
  </svg>
  <h2 class="abs heading" style="left:136px;top:2165px;color:var(--teal)">CELEBRATING</h2>
  <h2 class="abs heading" style="left:136px;top:2204px">LIFE WITH FAMILY</h2>
  <p class="abs para" style="left:136px;top:2278px;width:360px;font-size:14px;line-height:22px">Lorem ipsum dolor sit amet, consectetur adipiscing elit, sed do eiusmod tempor incididunt ut labore et dolore magna aliqua. Ut enim ad minim veniam, quis nostrud exercitation ullamco laboris nisi ut aliquip ex ea commodo consequat.</p>
  <a class="abs" style="left:136px;top:2413px;width:165px;height:42px;border:2px solid var(--teal);color:var(--teal);font-size:13px;font-weight:700;display:flex;align-items:center;justify-content:center">LEARN MORE</a>
</section>

<!-- RECIPES -->
<section>
  <div class="abs recipes"></div>
  <h2 class="abs heading" style="left:0;width:1200px;top:2632px;text-align:center;color:var(--white)">OUR RECIEPES</h2>
  <div class="abs" style="left:572px;top:2678px;width:66px;height:3px;background:var(--white)"></div>
  <article class="recipe" style="left:117px;border-radius:44px 0 0 0" role="img" aria-label="Rum cocktail over ice with a lime wedge">
    <h3>CRANBERRY THISTLE</h3><div class="rule"></div>
    <ul><li>Pour all ingredients in a shaker</li><li>Shake vigorously 10 seconds</li><li>Pour Mix in Highball Glass</li><li>Garnish Orange wedge</li></ul>
    <a class="pill">LEARN MORE</a>
  </article>
  <article class="recipe" style="left:617px;border-radius:44px 44px 0 0" role="img" aria-label="Old fashioned with an ice cube and orange peel">
    <h3>OLD FASHION TIDE</h3><div class="rule"></div>
    <ul><li>Pour all ingredients in a shaker</li><li>Shake vigorously 10 seconds</li><li>Pour in glass/ Ice ball</li><li>Garnish w/Orange skin</li></ul>
    <a class="pill">LEARN MORE</a>
  </article>
  <svg class="abs" style="left:0;top:3100px" width="1200" height="120" viewBox="0 0 1200 120">
    <path d="M0 108 Q600 -24 1200 108 L1200 120 L0 120 Z" fill="#fff"/>
    <path d="M0 100 Q600 -36 1200 100" fill="none" stroke="var(--gold)" stroke-width="4"/>
  </svg>
</section>

<!-- NEWS -->
<section>
  <div class="abs script" style="left:0;width:1200px;text-align:center;top:3198px;font-size:40px">Latest update</div>
  <h2 class="abs heading" style="left:0;width:1200px;top:3237px;text-align:center">NEWS &amp; EVENT</h2>
  <div class="abs" style="left:575px;top:3286px;width:50px;height:3px;background:var(--teal)"></div>

  <div class="photo" style="left:132px;top:3336px;width:485px;height:382px;background:linear-gradient(180deg,#4a86c8 0%,#9cc2e6 35%,#7d8a88 55%,#3a3f40 80%,#1c1c1c 100%)" role="img" aria-label="Distillery still house with a windmill under blue sky"></div>
  <div class="badge" style="left:178px;top:3608px;width:92px;height:20px">28 MAY 2021</div>
  <div class="abs" style="left:170px;top:3643px;width:420px;color:var(--white);font-size:17px;font-weight:700;line-height:20px">Lorem ipsum dolor sit amet, consectetur ad-ipiscing elit, sed do eiusmod tempor</div>

  <div class="photo" style="left:627px;top:3336px;width:216px;height:182px;background:linear-gradient(180deg,#5b8fc8,#7e7a6a 45%,#4a3a2a)" role="img" aria-label="Stacked rum barrels beneath palm trees"></div>
  <div class="news-box" style="top:3336px">
    <div class="badge" style="left:15px;top:34px;width:88px;height:20px">19 MAY 2021</div>
    <h4>Lorem ipsum dolor sit</h4>
    <p>Duis aute irure dolor in repre-henderit in voluptate velit esse cillum dolore eu fugiat</p>
  </div>
  <div class="photo" style="left:627px;top:3536px;width:216px;height:182px;background:linear-gradient(150deg,#1a1614,#5a2c12 50%,#a05a20 75%,#2a1a12)" role="img" aria-label="Snifter glasses of dark rum on a table"></div>
  <div class="news-box" style="top:3536px">
    <div class="badge" style="left:15px;top:34px;width:88px;height:20px">18 MAY 2021</div>
    <h4>Lorem ipsum dolor sit</h4>
    <p>Duis aute irure dolor in repre-henderit in voluptate velit esse cillum dolore eu fugiat</p>
  </div>
</section>

<!-- FOOTER -->
<footer class="abs footer">
  <div class="abs" style="left:214px;top:67px;width:72px;height:72px;border-radius:50%;border:3px solid var(--white)"></div>
  <div class="abs" style="left:120px;top:148px;width:260px;text-align:center;font-family:var(--serif);font-weight:600;font-size:30px">TIDE &amp; THISTLE</div>
  <span class="social" style="left:166px" aria-label="Social page"></span>
  <span class="social" style="left:211px" aria-label="Social page"></span>
  <span class="social" style="left:255px" aria-label="Social page"></span>
  <span class="social" style="left:300px" aria-label="Social page"></span>

  <div class="vline" style="left:421px"></div>
  <div class="vline" style="left:658px"></div>
  <div class="vline" style="left:873px"></div>

  <h5 style="left:450px;top:84px">QUICK LINKS</h5>
  <a style="left:455px;top:127px">About Us</a>
  <a style="left:455px;top:157px">Receipes</a>
  <a style="left:455px;top:186px">Products</a>
  <a style="left:455px;top:216px">News &amp; Events</a>

  <h5 style="left:694px;top:84px">RESOURCES</h5>
  <a style="left:696px;top:127px">Shipping &amp; Return</a>
  <a style="left:696px;top:157px">Support</a>
  <a style="left:696px;top:186px">Privacy Policy</a>
  <a style="left:696px;top:216px">Contact</a>

  <h5 style="left:908px;top:84px">CONTACT US</h5>
  <svg class="abs" style="left:915px;top:127px" width="16" height="22" viewBox="0 0 16 22"><path d="M8 1a7 7 0 0 0-7 7c0 5 7 13 7 13s7-8 7-13a7 7 0 0 0-7-7z" fill="#fff"/><circle cx="8" cy="8" r="2.6" fill="#2cc2a6"/></svg>
  <div class="contact" style="top:127px">48 Harbor Mill Lane<br>Port Averly, IL 60990</div>
  <svg class="abs" style="left:915px;top:178px" width="18" height="18" viewBox="0 0 24 24"><path d="M6.6 10.8a15 15 0 0 0 6.6 6.6l2.2-2.2a1 1 0 0 1 1-.25 11.4 11.4 0 0 0 3.6.57 1 1 0 0 1 1 1V20a1 1 0 0 1-1 1A17 17 0 0 1 3 4a1 1 0 0 1 1-1h3.5a1 1 0 0 1 1 1c0 1.25.2 2.45.57 3.57a1 1 0 0 1-.25 1z" fill="#fff"/></svg>
  <div class="contact" style="top:180px">(555) 014-2290</div>
  <svg class="abs" style="left:915px;top:216px" width="20" height="14" viewBox="0 0 20 14"><rect width="20" height="14" rx="1.5" fill="#fff"/><path d="M1 1 L10 8 L19 1" fill="none" stroke="#2cc2a6" stroke-width="1.6"/></svg>
  <div class="contact" style="top:216px">hello@tidethistle.com</div>

  <div class="abs" style="left:0;width:1200px;top:368px;text-align:center;font-size:10px;color:rgba(255,255,255,.9)">© 2021 Tide &amp; Thistle | All Rights Reserved</div>
</footer>

</body>
</html>
```